Hello my Name is Elias Moreno. I buy and sell vintage comic books, you can refer to my instragram page qpkz.comics to get ideas and inspiration. For the front of the card I would like my company logo QPKZ Comics with a yellow and black background with the bat signal or bat emblem like on my IG page and with my info Elias Moreno as the Owner and address/ phone number, PO Box 617283, Miami, FL 33827, 305-482-6170 and that I buy and sell comics & collectables . Also feel free to be open to other ideas if you want. Im not stuck on one design. For the back of the card I would like for it to say follow me on Instagram QPKZ.Comics with the ig emblem. Also would like the card to be vertical if possible. Thanks

```html
<!DOCTYPE html>
<html lang="en">
<head>
<meta charset="utf-8">
<title>QPKZ Comics – Business Card</title>
<link rel="stylesheet" href="https://fonts.googleapis.com/css2?family=Michroma&family=Roboto:wght@400;500&display=swap">
<style>
  :root {
    --stage: #1d1d1f;
    --yellow: #fbc51c;
    --yellow-deep: #e9b210;
    --ink: #0d0d0d;
    --paper: #ffffff;
    --font-display: "Michroma", "Arial", sans-serif;
    --font-body: "Roboto", "Arial", sans-serif;
  }
  * { box-sizing: border-box; margin: 0; padding: 0; }
  html, body { width: 1200px; height: 987px; overflow: hidden; }
  body {
    background: var(--stage);
    position: relative;
    font-family: var(--font-body);
    color: var(--ink);
  }
  .card {
    position: absolute;
    top: 184px;
    width: 380px;
    height: 620px;
    overflow: hidden;
    box-shadow: 0 18px 40px rgba(0,0,0,.55);
  }
  .card--front { left: 170px; background: var(--paper); }
  .card--back  { left: 650px; background: var(--yellow); }

  /* front */
  .front-wave { position: absolute; inset: 0; width: 100%; height: 100%; }
  .logo-tile {
    position: absolute;
    left: 95px; top: 58px;
    width: 190px; height: 190px;
    background: var(--yellow);
    display: flex; align-items: center; justify-content: center; gap: 8px;
  }
  .brand-mark {
    width: 18px; height: 18px; border-radius: 50%;
    background: var(--ink); flex: none;
  }
  .brand-name {
    font-family: var(--font-display);
    font-size: 15px;
    color: var(--ink);
    line-height: 1.25;
    text-align: left;
  }
  .contact {
    position: absolute;
    left: 0; right: 0; top: 372px;
    text-align: center;
  }
  .contact__name {
    font-family: var(--font-display);
    font-size: 19px;
    letter-spacing: 1px;
    text-transform: uppercase;
  }
  .contact__role { font-size: 14px; margin-top: 8px; text-transform: uppercase; }
  .contact__address { font-size: 15px; line-height: 1.3; margin-top: 16px; }
  .contact__lines { margin-top: 16px; font-size: 15px; line-height: 1.35; list-style: none; }
  .contact__lines li { display: flex; align-items: center; justify-content: center; gap: 6px; }
  .contact__lines svg { width: 13px; height: 13px; flex: none; }

  /* back */
  .flock {
    position: absolute; left: 0; top: 0; width: 100%; height: 150px;
    background: linear-gradient(180deg, var(--yellow-deep) 0%, var(--yellow) 100%);
  }
  .back-brand {
    position: absolute; left: 0; right: 0; top: 370px;
    display: flex; align-items: center; justify-content: center; gap: 10px;
  }
  .back-brand .brand-name { font-size: 19px; }
  .back-brand .brand-mark { width: 22px; height: 22px; }
  .social {
    position: absolute; left: 0; right: 0; top: 478px;
    display: flex; align-items: center; justify-content: center; gap: 7px;
    font-size: 17px;
  }
  .social__square {
    width: 17px; height: 17px; border: 2px solid var(--ink); border-radius: 4px;
  }
  .tagline {
    position: absolute; left: 0; right: 0; top: 512px;
    text-align: center;
    font-family: var(--font-display);
    font-size: 15px;
    line-height: 1.45;
    text-transform: uppercase;
    letter-spacing: .5px;
  }
</style>
</head>
<body>

  <section class="card card--front" aria-label="Card front">
    <svg class="front-wave" viewBox="0 0 380 620" preserveAspectRatio="none" aria-hidden="true">
      <path d="M0 330 C90 262 200 312 280 280 C320 264 350 246 380 236 L380 620 L0 620 Z" fill="#0d0d0d"/>
      <path d="M0 346 C95 282 205 326 285 296 C325 282 352 262 380 250 L380 620 L0 620 Z" fill="#ffffff"/>
      <path d="M0 354 C100 296 210 334 290 306 C330 292 355 272 380 262 L380 620 L0 620 Z" fill="#fbc51c"/>
    </svg>

    <div class="logo-tile">
      <span class="brand-mark"></span>
      <span class="brand-name">QPKZ<br>Comics</span>
    </div>

    <div class="contact">
      <h1 class="contact__name">Elias Moreno</h1>
      <p class="contact__role">Owner</p>
      <p class="contact__address">PO Box 617283<br>Miami, FL 33827</p>
      <ul class="contact__lines">
        <li>
          <svg viewBox="0 0 16 16" aria-hidden="true"><path fill="#0d0d0d" d="M3.6 1.2l2.3 2.6-1.3 1.8c.9 2 2.5 3.6 4.5 4.6l1.8-1.3 2.6 2.3-1.4 2.4C6.8 13.4 2.6 9.2 1.2 2.6z"/></svg>
          305-482-6170
        </li>
        <li>
          <svg viewBox="0 0 16 16" aria-hidden="true"><rect x="1" y="3" width="14" height="10" fill="#0d0d0d"/><path d="M1 3.5l7 5 7-5" stroke="#fbc51c" stroke-width="1.3" fill="none"/></svg>
          hello@qpkzmail.com
        </li>
        <li>
          <svg viewBox="0 0 16 16" aria-hidden="true"><circle cx="8" cy="8" r="7" fill="#0d0d0d"/><path d="M1 8h14M8 1c-3 3-3 11 0 14M8 1c3 3 3 11 0 14" stroke="#fbc51c" stroke-width="1" fill="none"/></svg>
          www.qpkzcomics.com
        </li>
      </ul>
    </div>
  </section>

  <section class="card card--back" aria-label="Card back">
    <div class="flock" role="img" aria-label="Flock of black bats flying across the top of the card"></div>

    <div class="back-brand">
      <span class="brand-mark"></span>
      <span class="brand-name">QPKZ Comics</span>
    </div>

    <p class="social"><span class="social__square"></span>QPKZ.Comics</p>

    <p class="tagline">Buy &amp; Sell Comics<br>&amp; Collectables</p>
  </section>

</body>
</html>
```